Stylish Business Cards Wanted

- DOUBLE SIDED Design Required -

High end, edgy cards for a corporate and personal stylist. Must include logo,
Name: Belinda Harwick
Title: Director and Stylist
telephone : +61 8 7142 5809
email: belinda@theloombriefing.example
website: theloombriefing.example
Tag: Corporate Workwear & Uniform Specialist | Personal Stylist
Would like nice icons for telephone, email, website

Target Market(s)

Businesses wanting stylish uniforms, people wanting stylish wardrobes

Industry/Entity Type

Corporate Workwear Stylist

Contact Information for Business Card

I would like black, white and gold foiling incorporated in the design - possibly a touch of the other colours on my branding guide attached Name: Belinda Harwick Title: Director and Stylist telephone : +61 8 7142 5809 email: belinda@theloombriefing.example website: theloombriefing.example Tag: Corporate Workwear & Uniform Specialist | Personal Stylist Would like nice icons for telephone, email, website

Font styles to use
Other font styles liked:
• Raleway

Colors

Designer to choose colors to be used in the design.

Requirements
Must have
• Gold foil accents

```html
<!DOCTYPE html>
<html lang="en">
<head>
<meta charset="utf-8">
<title>The Loom Briefing – Business Cards</title>
<link href="https://fonts.googleapis.com/css2?family=Montserrat:wght@400;500;600;700&display=swap" rel="stylesheet">
<style>
  :root {
    --backdrop: #171717;
    --card: #232323;
    --card-edge: #1b1b1b;
    --gold: #e8b94f;
    --white: #ffffff;
    --ghost: #1c1c1c;
  }
  * { margin: 0; padding: 0; box-sizing: border-box; }
  html, body {
    width: 1200px; height: 988px; overflow: hidden;
    background: var(--backdrop);
    font-family: "Montserrat", Arial, sans-serif;
  }
  .canvas { position: relative; width: 1200px; height: 988px; }

  .card {
    position: absolute;
    width: 640px; height: 356px;
    background: var(--card);
    overflow: hidden;
    box-shadow: 0 18px 40px rgba(0,0,0,.55);
  }
  .card--front { left: 70px; top: 80px; }
  .card--back { left: 490px; top: 552px; }

  /* brand wordmark */
  .brand {
    position: absolute;
    color: var(--white);
    font-weight: 600;
    text-transform: uppercase;
    letter-spacing: 3px;
    line-height: 1.1;
    text-align: center;
  }
  .card--front .brand {
    left: 0; right: 0; top: 110px;
    font-size: 40px;
  }
  .card--back .brand {
    left: 40px; top: 40px;
    font-size: 26px;
    text-align: left;
  }

  .tagline {
    position: absolute;
    left: 0; right: 0; bottom: 56px;
    text-align: center;
    color: var(--gold);
    font-size: 15px;
    font-weight: 500;
    letter-spacing: .3px;
  }

  /* back side */
  .ghost-mark {
    position: absolute;
    right: 20px; top: 30px;
    color: var(--ghost);
    font-size: 88px;
    font-weight: 700;
    text-transform: uppercase;
    letter-spacing: 4px;
    line-height: 1;
  }
  .accent-dot {
    position: absolute;
    left: -18px; top: 170px;
    width: 36px; height: 36px;
    border-radius: 50%;
    background: var(--gold);
  }
  .person { position: absolute; left: 40px; top: 166px; }
  .person__name {
    color: var(--gold);
    font-size: 22px;
    font-weight: 700;
    text-transform: uppercase;
    letter-spacing: 1px;
  }
  .person__title {
    color: var(--white);
    font-size: 14px;
    margin-top: 2px;
  }
  .contacts {
    position: absolute; left: 40px; top: 250px;
    list-style: none;
  }
  .contact {
    display: flex; align-items: center; gap: 10px;
    color: var(--white);
    font-size: 13px;
    margin-bottom: 10px;
  }
  .contact svg { width: 15px; height: 15px; flex: none; }
  .contact--web {
    position: absolute; right: 40px; top: 262px;
  }
  .gold-bar {
    position: absolute;
    right: 0; bottom: 0;
    width: 300px; height: 10px;
    background: var(--gold);
  }
</style>
</head>
<body>
<div class="canvas">

  <section class="card card--front" aria-label="Card front">
    <div class="brand">The Loom<br>Briefing</div>
    <p class="tagline">Corporate Workwear &amp; Uniform Specialist | Personal Stylist</p>
  </section>

  <section class="card card--back" aria-label="Card back">
    <div class="ghost-mark" aria-hidden="true">Loom</div>
    <div class="brand">The Loom<br>Briefing</div>
    <span class="accent-dot"></span>
    <div class="person">
      <h1 class="person__name">Belinda Harwick</h1>
      <p class="person__title">Director and Stylist</p>
    </div>
    <ul class="contacts">
      <li class="contact">
        <svg viewBox="0 0 24 24" aria-hidden="true"><path fill="#e8b94f" d="M6.6 10.8a15.1 15.1 0 0 0 6.6 6.6l2.2-2.2a1 1 0 0 1 1-.25 11.4 11.4 0 0 0 3.6.6 1 1 0 0 1 1 1V20a1 1 0 0 1-1 1A17 17 0 0 1 3 4a1 1 0 0 1 1-1h3.5a1 1 0 0 1 1 1c0 1.25.2 2.45.6 3.6a1 1 0 0 1-.25 1z"/></svg>
        +61 8 7142 5809
      </li>
      <li class="contact">
        <svg viewBox="0 0 24 24" aria-hidden="true"><rect x="2" y="5" width="20" height="14" rx="1" fill="#e8b94f"/><path d="M2 6l10 7 10-7" fill="none" stroke="#232323" stroke-width="1.6"/></svg>
        belinda@theloombriefing.example
      </li>
    </ul>
    <div class="contact contact--web">
      <svg viewBox="0 0 24 24" aria-hidden="true"><circle cx="12" cy="12" r="10" fill="#e8b94f"/><path d="M2 12h20M12 2c3 3 3 17 0 20M12 2c-3 3-3 17 0 20" fill="none" stroke="#232323" stroke-width="1.4"/></svg>
      www.theloombriefing.example
    </div>
    <span class="gold-bar"></span>
  </section>

</div>
</body>
</html>
```